Professional and creative business card design for recruiting service providers

Our company supports German medium-sized companies in filling vacancies promptly. For this we use social media marketing and bring our customers into the visibility.

We want a professional but also creative design for our business cards.

Please look at lindqvar-staff.de to get an impression of our CI.

Target Market(s)

Small and medium-sized companies in Germany from the industry

Industry/Entity Type

Industrie, Handwerk

Contact Information for Business Card

Name, Position, Telefonnummer, Email, Website

Colors
EE7325
F08F49
F5BC92
FAE3D3
FDF4ED

Requirements
Must have
• A picture of the employee and in the style of www.lindqvar-staff.de

```html
<!DOCTYPE html>
<html lang="de">
<head>
<meta charset="utf-8">
<title>Lindqvar &amp; Staff – Visitenkarte</title>
<link rel="stylesheet" href="https://fonts.googleapis.com/css2?family=Montserrat:wght@700&family=Arimo:wght@400&display=swap">
<style>
  :root {
    --page: #e6e6e6;
    --card: #2e2e2e;
    --card-deep: #262626;
    --orange: #ee7325;
    --orange-strong: #e8592a;
    --white: #ffffff;
    --photo-light: #5a5350;
    --photo-dark: #1a1a1c;
  }
  * { box-sizing: border-box; margin: 0; padding: 0; }
  html, body {
    width: 1200px; height: 802px; overflow: hidden;
    background: var(--page);
  }
  .stage {
    position: relative; width: 1200px; height: 802px;
    display: flex; align-items: center; justify-content: center; gap: 40px;
  }
  .card {
    position: relative; width: 540px; height: 336px;
    background: var(--card); overflow: hidden;
    box-shadow: 0 6px 18px rgba(0,0,0,.18);
  }

  /* Front */
  .portrait {
    position: absolute; left: 18px; top: 70px; width: 250px; height: 266px;
    background: radial-gradient(ellipse at 45% 30%, var(--photo-light) 0%, #3a3433 35%, var(--photo-dark) 80%);
  }
  .brand {
    position: absolute; display: flex; align-items: center; gap: 12px;
    font-family: "Montserrat", sans-serif; font-weight: 700;
    color: var(--white); text-transform: uppercase; letter-spacing: 1.5px;
  }
  .brand__square { background: var(--orange); flex: none; }
  .brand__name { line-height: 1.05; }
  .card--front .brand { left: 250px; top: 34px; font-size: 24px; }
  .card--front .brand__square { width: 34px; height: 34px; }

  .person {
    position: absolute; right: 30px; top: 112px; text-align: right;
  }
  .person__name {
    font-family: "Montserrat", sans-serif; font-weight: 700; font-size: 19px;
    color: var(--orange-strong); text-transform: uppercase; letter-spacing: .5px;
  }
  .person__role {
    font-family: "Arimo", sans-serif; font-size: 15px; color: var(--white); margin-top: 2px;
  }
  .contact {
    position: absolute; right: 30px; top: 176px; list-style: none;
    font-family: "Arimo", sans-serif; font-size: 14px; color: var(--white);
  }
  .contact li {
    display: flex; align-items: center; justify-content: flex-end; gap: 8px;
    line-height: 21px;
  }
  .contact svg { width: 12px; height: 12px; flex: none; }

  .address {
    position: absolute; left: 268px; right: 0; bottom: 0; height: 66px;
    background: var(--orange-strong);
    display: flex; flex-direction: column; justify-content: center; align-items: flex-end;
    padding-right: 30px;
    font-family: "Arimo", sans-serif; font-size: 15px; color: var(--white); line-height: 1.3;
  }

  /* Back */
  .pattern {
    position: absolute; inset: 0;
    background:
      linear-gradient(125deg, #232323 0%, #303030 45%, #4a4a4a 70%, #2c2c2c 100%);
  }
  .card--back .brand { right: 60px; top: 140px; font-size: 24px; }
  .card--back .brand__square { width: 40px; height: 40px; }
</style>
</head>
<body>
<main class="stage">

  <section class="card card--front" aria-label="Vorderseite">
    <div class="portrait" role="img" aria-label="Porträtfoto des Mitarbeiters vor dunklem Hintergrund"></div>

    <div class="brand">
      <span class="brand__square"></span>
      <span class="brand__name">Lindqvar<br>&amp; Staff</span>
    </div>

    <div class="person">
      <p class="person__name">Marek Holloway</p>
      <p class="person__role">Manager</p>
    </div>

    <ul class="contact">
      <li>0172 404 2317
        <svg viewBox="0 0 24 24" aria-hidden="true"><path fill="var(--orange)" d="M6.6 10.8a15.1 15.1 0 0 0 6.6 6.6l2.2-2.2a1 1 0 0 1 1-.25 11.4 11.4 0 0 0 3.6.57 1 1 0 0 1 1 1V20a1 1 0 0 1-1 1A17 17 0 0 1 3 4a1 1 0 0 1 1-1h3.5a1 1 0 0 1 1 1c0 1.25.2 2.45.57 3.57a1 1 0 0 1-.25 1z"/></svg>
      </li>
      <li>info@lindqvar-staff.de
        <svg viewBox="0 0 24 24" aria-hidden="true"><rect x="2" y="5" width="20" height="14" fill="none" stroke="var(--orange)" stroke-width="2"/><path d="M2 5l10 8 10-8" fill="none" stroke="var(--orange)" stroke-width="2"/></svg>
      </li>
      <li>www.lindqvar-staff.de
        <svg viewBox="0 0 24 24" aria-hidden="true"><circle cx="12" cy="12" r="10" fill="none" stroke="var(--orange)" stroke-width="2"/><path d="M2 12h20M12 2c3 3 3 17 0 20M12 2c-3 3-3 17 0 20" fill="none" stroke="var(--orange)" stroke-width="1.6"/></svg>
      </li>
    </ul>

    <div class="address">
      <span>Bergheimer Weg 17a</span>
      <span>70499 Stuttgart</span>
    </div>
  </section>

  <section class="card card--back" aria-label="Rückseite">
    <div class="pattern" role="img" aria-label="Geprägtes Muster aus dem Firmenzeichen in Dunkelgrau"></div>
    <div class="brand">
      <span class="brand__square"></span>
      <span class="brand__name">Lindqvar<br>&amp; Staff</span>
    </div>
  </section>

</main>
</body>
</html>
```